Stationery for a private security company, "Brenmoor Security Services Ltd."

Needed is a stationery design for a private security company. The designs must show professionalism and that our company mean nothing but business. Watermark of the company logo on the letterhead page is also a must. The final design must represent innovation and professionalism. It would be great if designers could integrate the colours black and silver onto the cards and letterheads..

Thank you

```html
<!DOCTYPE html>
<html lang="en">
<head>
<meta charset="utf-8">
<title>Brenmoor Security Services Ltd. – Business Card</title>
<link href="https://fonts.googleapis.com/css2?family=Didact+Gothic&display=swap" rel="stylesheet">
<style>
  :root {
    --backdrop: #3a3d3c;
    --card: #f7f7f7;
    --card-edge: #e6e6e6;
    --ink: #1c1c1c;
    --ink-soft: #3a3a3a;
    --silver: #c9c9c9;
    --silver-light: #e4e4e4;
  }
  * { margin: 0; padding: 0; box-sizing: border-box; }
  html, body {
    width: 1200px;
    height: 1000px;
    overflow: hidden;
    background: var(--backdrop);
    font-family: "Didact Gothic", "Century Gothic", sans-serif;
    color: var(--ink);
  }
  .sheet {
    width: 1200px;
    height: 1000px;
    display: flex;
    flex-direction: column;
    align-items: center;
    justify-content: center;
    gap: 48px;
  }
  .card {
    position: relative;
    width: 760px;
    height: 434px;
    background: var(--card);
    border: 1px solid var(--card-edge);
    overflow: hidden;
  }
  .watermark {
    position: absolute;
    right: -40px;
    bottom: -60px;
    width: 520px;
    height: 420px;
    border-radius: 50%;
    background: radial-gradient(ellipse at 45% 45%, var(--silver-light) 0%, rgba(228,228,228,0.55) 45%, rgba(247,247,247,0) 72%);
  }
  .brand {
    position: absolute;
    display: flex;
    align-items: center;
    gap: 12px;
    text-transform: uppercase;
    color: var(--ink);
    font-weight: 400;
  }
  .brand-dot {
    flex: none;
    border-radius: 50%;
    background: var(--ink);
  }
  .card--front .brand {
    left: 80px;
    top: 170px;
    font-size: 34px;
    letter-spacing: 2px;
    line-height: 1.15;
  }
  .card--front .brand-dot { width: 46px; height: 46px; }
  .card--back .brand {
    right: 40px;
    top: 36px;
    font-size: 16px;
    letter-spacing: 1px;
    line-height: 1.2;
    text-align: right;
  }
  .card--back .brand-dot { width: 22px; height: 22px; }
  .contact {
    position: absolute;
    left: 48px;
    top: 120px;
    text-transform: uppercase;
    font-size: 15px;
    letter-spacing: 0.6px;
    color: var(--ink-soft);
  }
  .contact-web {
    display: flex;
    align-items: center;
    gap: 8px;
    font-size: 16px;
    color: var(--ink);
  }
  .contact-web svg { flex: none; }
  .contact-name {
    margin-top: 40px;
    font-size: 20px;
    color: var(--ink);
    letter-spacing: 1px;
  }
  .contact-role { font-size: 13px; }
  .contact-lines { margin-top: 30px; line-height: 1.45; }
  .contact-lines .label { display: inline-block; width: 88px; }
  .contact-address { margin-top: 18px; line-height: 1.45; }
</style>
</head>
<body>
<main class="sheet">
  <section class="card card--front">
    <div class="watermark" role="img" aria-label="Faint silver company emblem watermark"></div>
    <div class="brand">
      <span class="brand-dot"></span>
      <span>Brenmoor<br>Security Services Ltd.</span>
    </div>
  </section>

  <section class="card card--back">
    <div class="watermark" role="img" aria-label="Faint silver company emblem watermark"></div>
    <div class="brand">
      <span>Brenmoor<br>Security Services Ltd.</span>
      <span class="brand-dot"></span>
    </div>
    <div class="contact">
      <div class="contact-web">
        <svg width="30" height="10" viewBox="0 0 30 10" aria-hidden="true">
          <g fill="none" stroke="#1c1c1c" stroke-width="1.6">
            <path d="M1 1l4 4-4 4M8 1l4 4-4 4M15 1l4 4-4 4M22 1l4 4-4 4"/>
          </g>
        </svg>
        <span>www.brenmoorsecurity.co.uk</span>
      </div>
      <div class="contact-name">Daniel Hart</div>
      <div class="contact-role">[Charge]</div>
      <div class="contact-lines">
        <div>dhart@brenmoorsecurity.co.uk</div>
        <div><span class="label">[ Phone ]</span>+44 800 555 0142</div>
        <div><span class="label">[ Fax ]</span>+44 0 800 555 0143</div>
      </div>
      <div class="contact-address">
        <div>Kestrel House | 24 Oakfield Road</div>
        <div>Ashvale | Surrey | GU12 4TQ.</div>
      </div>
    </div>
  </section>
</main>
</body>
</html>
```